Business Card Design Can you design a business card design? Looking for something unique and differe

Can you design a business card design? Looking for something unique and different. Can you design a business card design? Looking for something unique and different.Can you design a business card design? Looking for something unique and different.Can you design a business card design? Looking for something unique and different.Can you design a business card design? Looking for something unique and different.Can you design a business card design? Looking for something unique and different.

Industry/Entity Type

Business

Contact Information for Business Card

Can you design a business card design? Looking for something unique and different.

Font styles to use
Serif

```html
<!DOCTYPE html>
<html lang="en">
<head>
<meta charset="UTF-8">
<title>Veridon Business Card</title>
<link rel="stylesheet" href="https://fonts.googleapis.com/css2?family=Raleway:wght@400;500;600&display=swap">
<style>
  :root {
    --backdrop: #161617;
    --card: #2e2f33;
    --accent: #a07bb5;
    --muted: #c4c4c8;
    --light: #e6e6ea;
  }
  html, body {
    margin: 0;
    padding: 0;
    width: 1200px;
    height: 900px;
    overflow: hidden;
    background: var(--backdrop);
    font-family: "Raleway", sans-serif;
  }
  .canvas {
    position: relative;
    width: 1200px;
    height: 900px;
  }
  .card {
    position: absolute;
    background: var(--card);
    border-radius: 14px;
  }
  .card--front { left: 330px; top: 120px; width: 543px; height: 315px; }
  .card--back  { left: 331px; top: 489px; width: 541px; height: 314px; }

  .brand {
    position: absolute;
    left: 60px;
    top: 170px;
    width: 182px;
    display: flex;
    align-items: center;
    justify-content: center;
    gap: 10px;
  }
  .brand__square {
    width: 14px;
    height: 14px;
    background: var(--accent);
  }
  .brand__name {
    font-weight: 600;
    font-size: 31px;
    color: var(--accent);
    letter-spacing: 0.3px;
  }

  .contact {
    position: absolute;
    left: 284px;
    top: 112px;
  }
  .contact__name {
    margin: 0;
    font-weight: 500;
    font-size: 25px;
    line-height: 30px;
    color: var(--accent);
  }
  .contact__role {
    margin: 0;
    font-weight: 500;
    font-size: 16px;
    line-height: 20px;
    color: var(--muted);
  }
  .contact__details {
    margin: 20px 0 0 4px;
    font-size: 15px;
    line-height: 19px;
    color: var(--light);
  }

  .back-brand {
    position: absolute;
    inset: 0;
    display: flex;
    align-items: center;
    justify-content: center;
    font-weight: 600;
    font-size: 60px;
    color: var(--accent);
    letter-spacing: 1px;
  }
</style>
</head>
<body>
  <main class="canvas">
    <section class="card card--front">
      <div class="brand">
        <span class="brand__square"></span>
        <span class="brand__name">Veridon</span>
      </div>
      <div class="contact">
        <h1 class="contact__name">Daniel Hart</h1>
        <p class="contact__role">Managing Director</p>
        <p class="contact__details">hello@veridon.com<br>044-987 654 321</p>
      </div>
    </section>
    <section class="card card--back">
      <div class="back-brand">Veridon</div>
    </section>
  </main>
</body>
</html>
```